NZ First of it's kind solutions directory and marketplace for busy Mums needs a business card design

We need a business card design for our new nationwide business in NZ (long term plans to go global). We provide solutions to the everyday challenges that busy Mums face by connecting them with quality communities and suppliers of carefully selected, relevant products and services. We sell direct via our online marketplace. The final design should communicate our values of inclusivity, quality and smart solutions. Colours should incorporate our logo colour palette of #477077 and #6ba8b2. Our website is at https://www.brightnestmums.example

Target Market(s)

busy Mums, Age 28 – 50, female, income over $100K, location main centres NZ primarily but NZ wide. Is likely juggling work or career with a young family. Probably had hobbies which have fallen by the wayside.
-Wants to succeed in her chosen career without compromising on family life
-to successfully juggle her career without feeling like she is compromising her children
- Is time poor, something always has to give and it’s generally her health (she’ll stay up late, get stressed)
- probably ex corporate or professional career. Has discretional income

Industry/Entity Type

Business

Contact Information for Business Card

Lena Forbisher, Founder, BrightNestMums.example (Strapline Tap; Gather; Sorted), 47 Kowhai Terrace, Ellerslie, Auckland 1051, New Zealand. Mob: 021 483 517 Ph: +64 (0)9 571 4860

Font styles to use
Other font styles liked:
• Raleway, and/or Architects Daughter

Colors
00a990
33b8a4
86cfc6
cfeae6

Requirements
Must have
• the above details, streamline. the logo and colours associated with those logos
Should not have
• foil or metallic colours

```html
<!DOCTYPE html>
<html lang="en">
<head>
<meta charset="utf-8">
<title>BrightNestMums business card</title>
<link rel="stylesheet" href="https://fonts.googleapis.com/css2?family=Roboto:wght@400;500;700&family=Roboto+Condensed:wght@400;700&display=swap">
<style>
  :root {
    --teal-deep: #477077;
    --teal-light: #6ba8b2;
    --ink: #3d4346;
    --rule: #c4c9cb;
    --paper: #ffffff;
    --stage: #e9eceb;
  }
  * { margin: 0; padding: 0; box-sizing: border-box; }
  html, body { width: 1200px; height: 886px; overflow: hidden; }
  body {
    background: var(--stage);
    font-family: "Roboto", Arial, sans-serif;
    display: flex;
    align-items: center;
    justify-content: center;
    gap: 40px;
  }
  .card {
    position: relative;
    width: 540px;
    height: 309px;
    border-radius: 3px;
    overflow: hidden;
    box-shadow: 0 6px 18px rgba(0,0,0,.14);
  }
  .card-front { background: var(--paper); color: var(--ink); }
  .card-back {
    background: linear-gradient(160deg, #507b82 0%, var(--teal-deep) 100%);
    display: flex; align-items: center; justify-content: center; gap: 14px;
  }
  .brand {
    position: absolute; top: 66px; left: 0; right: 0;
    display: flex; align-items: center; justify-content: center; gap: 12px;
  }
  .brand-dot {
    width: 30px; height: 30px; border-radius: 50%;
    background: var(--teal-light);
  }
  .brand-name {
    font-family: "Roboto Condensed", "Arial Narrow", sans-serif;
    font-weight: 700; font-size: 34px; letter-spacing: -0.5px;
    color: var(--teal-deep);
  }
  .divider {
    position: absolute; top: 146px; left: 40px; right: 40px;
    height: 1px; background: var(--rule);
  }
  .person { position: absolute; left: 40px; top: 178px; }
  .person-name {
    font-family: "Roboto Condensed", "Arial Narrow", sans-serif;
    font-weight: 700; font-size: 19px; color: var(--teal-deep);
    text-transform: uppercase; line-height: 1.1;
  }
  .person-role {
    font-family: "Roboto Condensed", "Arial Narrow", sans-serif;
    font-size: 14px; color: var(--teal-light); text-transform: uppercase;
  }
  .contact-list { list-style: none; margin-top: 10px; font-size: 12.5px; line-height: 17px; }
  .contact-list li { display: flex; align-items: center; gap: 8px; }
  .contact-list svg { width: 10px; height: 10px; fill: var(--ink); }
  .address {
    position: absolute; right: 40px; top: 180px;
    text-align: right; font-size: 13px; line-height: 18px;
  }
  .base-bands { position: absolute; left: 0; bottom: 0; width: 540px; height: 60px; }
  .strapline {
    position: absolute; right: 16px; bottom: 16px;
    color: #fff; font-size: 11.5px; letter-spacing: .6px; text-transform: uppercase;
  }
  .back-dot { width: 44px; height: 44px; border-radius: 50%; background: #fff; }
  .back-name {
    font-family: "Roboto Condensed", "Arial Narrow", sans-serif;
    font-weight: 700; font-size: 30px; color: #fff;
  }
</style>
</head>
<body>
  <section class="card card-front">
    <div class="brand">
      <span class="brand-dot"></span>
      <span class="brand-name">BrightNestMums</span>
    </div>
    <div class="divider"></div>

    <div class="person">
      <p class="person-name">Lena Forbisher</p>
      <p class="person-role">Founder</p>
      <ul class="contact-list">
        <li><svg viewBox="0 0 10 10"><path d="M2 0l2 2-1 1.5c.6 1.3 1.6 2.3 3 3L7.5 5.5l2 2L8 10C4 9.5.5 6 0 2z"/></svg>+64 (0)9 571 4860</li>
        <li><svg viewBox="0 0 10 10"><path d="M2 0h6v10H2zM3 1v7h4V1z"/></svg>021 483 517</li>
        <li><svg viewBox="0 0 10 10"><circle cx="5" cy="5" r="5"/></svg>BrightNestMums.example</li>
      </ul>
    </div>

    <address class="address" style="font-style:normal">
      47 Kowhai Terrace, Ellerslie<br>
      Auckland 1051, New Zealand
    </address>

    <svg class="base-bands" viewBox="0 0 540 60" aria-hidden="true">
      <rect x="0" y="44" width="42" height="16" fill="var(--teal-deep)"/>
      <polygon points="60,60 60,53 380,53 392,40 540,40 540,60" fill="var(--teal-light)"/>
      <polygon points="398,8 540,8 540,46 386,46 386,20" fill="var(--teal-deep)"/>
    </svg>
    <p class="strapline">Tap, Gather, Sorted</p>
  </section>

  <section class="card card-back">
    <span class="back-dot"></span>
    <span class="back-name">BrightNestMums</span>
  </section>
</body>
</html>
```